Business card for a new innovative and professional lawn care business

We need a business card design for a new lawn care business in Halifax NS Canada. We offer lawn services in Halifax & Bedford. Our services offered include lawn care, garden services, and property maintenance. We take pride in our work and are experienced at what we do. I would like to see a design that is double sided. On the backside I would like the something simple (maybe my logo preferably on blackround (linked below) with website link, Linkhub page or something). The front I want to include contact info:
Morgan Pell
phone 902-555-0148
email - brookvaleyards.ca
facebook - linkhub.ca/brookvaleyards
Snapfeed maybe ? - snapfeed.ca/brookvaleyard
Serving Halifax and Bedford for 5 years?
I don't want it to have too much information as I will be passing them out in aim to visit website, or call !
We do want it to include lawn care, garden services and property maintenance.
Basic, catchy, and modern looking !
Logo attached below !

Target Market(s)

Passing business cards to everyone I meet or interact with.

Industry/Entity Type

Lawn Care

Contact Information for Business Card

Double sided with some basic information, with catchy colours and easy to look at.

Font styles to use
Sans Serif

Requirements
Must have
• Must be double sided and have :
• Name, Phone, Email, FB, Website, and 3 main services offered - lawn care, property maintenance, garden services
Nice to have
• Would be nice to have instagram link if it goes well on there
Should not have
• Don't want too much writing or images that are distracting

```html
<!DOCTYPE html>
<html lang="en">
<head>
<meta charset="utf-8">
<title>Brookvale Yards – Business Card</title>
<link href="https://fonts.googleapis.com/css2?family=Cabin:wght@400;600;700&display=swap" rel="stylesheet">
<style>
  :root {
    --backdrop: #005f1f;
    --card-white: #ffffff;
    --ink: #1a1a1a;
    --lime: #7fc31c;
    --lime-line: #a6d45a;
    --band: rgba(0, 0, 0, 0.78);
    --grass-light: #6fbf2a;
    --grass-deep: #2f7d14;
    --fence: #6b5a48;
    --hedge: #2c5a1c;
    --icon: #333333;
  }
  * { box-sizing: border-box; margin: 0; padding: 0; }
  html, body { width: 1200px; height: 1000px; overflow: hidden; }
  body {
    background: var(--backdrop);
    font-family: "Cabin", sans-serif;
    color: var(--ink);
    position: relative;
  }
  .card {
    position: absolute;
    left: 297px;
    width: 604px;
    height: 354px;
    border-radius: 14px;
    overflow: hidden;
    border: 1px solid #111;
    box-shadow: -10px 10px 10px rgba(0, 0, 0, 0.45);
  }
  .card--front { top: 132px; }
  .card--back { top: 512px; background: var(--card-white); }

  .front-photo {
    position: absolute; inset: 0;
    background:
      linear-gradient(180deg, var(--fence) 0%, #7d6a56 22%, var(--hedge) 34%, #3a6a22 44%, var(--grass-light) 52%, var(--grass-deep) 100%);
  }
  .front-band {
    position: absolute; left: 0; right: 0; top: 195px; height: 113px;
    background: var(--band);
    display: flex; align-items: center; justify-content: center; gap: 12px;
  }
  .brand-name {
    font-family: "Cabin", sans-serif;
    font-weight: 700;
    color: var(--lime);
    letter-spacing: 1px;
    white-space: nowrap;
  }
  .brand-dot {
    border-radius: 50%;
    background: var(--lime);
    flex: none;
  }
  .front-band .brand-name { font-size: 40px; }
  .front-band .brand-dot { width: 26px; height: 26px; }
  .services {
    position: absolute; left: 0; right: 0; top: 308px;
    text-align: center;
    font-size: 21px; font-weight: 600;
    color: #111;
    white-space: nowrap;
  }
  .services .sep { margin: 0 7px; font-weight: 400; }

  .back-brand {
    position: absolute; left: 0; right: 0; top: 52px;
    display: flex; align-items: center; justify-content: center; gap: 12px;
  }
  .back-brand .brand-name { font-size: 40px; }
  .back-brand .brand-dot { width: 26px; height: 26px; }
  .holder-name {
    position: absolute; left: 0; right: 0; top: 222px;
    text-align: center;
    font-size: 20px; font-weight: 600;
    font-variant: small-caps;
    letter-spacing: 0.3px;
  }
  .divider {
    position: absolute; left: 28px; right: 28px; top: 265px;
    height: 2px; background: var(--lime-line);
  }
  .contact-row {
    position: absolute; left: 0; right: 0;
    display: flex; justify-content: center; align-items: center;
    font-size: 15px;
    white-space: nowrap;
  }
  .contact-row--primary { top: 280px; gap: 26px; }
  .contact-row--social { top: 311px; gap: 26px; }
  .contact-item { display: flex; align-items: center; gap: 12px; }
  .contact-item svg { flex: none; }
  .social-square { width: 19px; height: 19px; background: var(--icon); flex: none; }
</style>
</head>
<body>
  <section class="card card--front">
    <div class="front-photo" role="img" aria-label="Photo of a lawn mower on a freshly cut green lawn beside a wooden fence lined with cedar shrubs"></div>
    <div class="front-band">
      <span class="brand-dot"></span>
      <span class="brand-name">BROOKVALE YARDS</span>
    </div>
    <p class="services">Lawn Care<span class="sep">|</span>Garden Services<span class="sep">|</span>Property Maintenance</p>
  </section>

  <section class="card card--back">
    <div class="back-brand">
      <span class="brand-dot"></span>
      <span class="brand-name">BROOKVALE YARDS</span>
    </div>
    <p class="holder-name">Morgan Pell</p>
    <div class="divider"></div>
    <div class="contact-row contact-row--primary">
      <span class="contact-item">
        <svg width="20" height="20" viewBox="0 0 20 20" aria-hidden="true">
          <circle cx="10" cy="10" r="8.5" fill="none" stroke="#333" stroke-width="1.2"/>
          <path d="M8 5.5c-1.5 1-1.8 3-.8 5s2.6 3.6 4.4 3.8l1.2-1.4-1.8-1.4-.9.6c-.9-.5-1.7-1.7-2-2.8l.9-.6-.6-2.1z" fill="#333"/>
        </svg>
        902-555-0148
      </span>
      <span class="contact-item">
        <svg width="32" height="20" viewBox="0 0 32 20" aria-hidden="true">
          <rect x="1" y="1" width="30" height="18" fill="none" stroke="#333" stroke-width="1.3"/>
          <path d="M1 1l15 11L31 1M1 19l11-9M31 19l-11-9" fill="none" stroke="#333" stroke-width="1.3"/>
        </svg>
        hello@brookvaleyards.ca
      </span>
      <span class="contact-item">
        <svg width="20" height="20" viewBox="0 0 20 20" aria-hidden="true">
          <g fill="none" stroke="#333" stroke-width="1.1">
            <circle cx="10" cy="10" r="8.5"/>
            <ellipse cx="10" cy="10" rx="3.8" ry="8.5"/>
            <path d="M1.5 10h17M3 5.5h14M3 14.5h14M10 1.5v17"/>
          </g>
        </svg>
        brookvaleyards.ca
      </span>
    </div>
    <div class="contact-row contact-row--social">
      <span class="contact-item"><span class="social-square"></span>linkhub.ca/brookvaleyards</span>
      <span class="contact-item"><span class="social-square"></span>snapfeed.ca/brookvaleyard</span>
    </div>
  </section>
</body>
</html>
```